Help design website for "Brightwater Civic Advisors" to advance the common good

Here is the Google doc link that lays out the design:

https://files.plumrivet.example/sheet/d/7QmTzR2wLx9KpVbN4hJcY8sEaUoFdG3iXkMnPq5rWt6/edit?usp=sharing

Here is the Google drive folder with the logos and photos: https://vault.plumrivet.example/open?id=4HkWp9LzQe2TxRvN8mBaYc3DsUoJfG6

The testimonials are being gathered and will be shared by Friday, 1/4.

The winner will also have to migrate the coding files to my hosting site.

Thank you for your help! Looking forward to seeing your designs.

Target Market(s)

Prospective clients

Industry/Entity Type

Non Profit

Coding

Coded - Design and coding required

Number of Pages Required

5+ page

Requirements
Must have
• Noted in the Google doc regarding layout.
Nice to have

```html
<!DOCTYPE html>
<html lang="en">
<head>
<meta charset="utf-8">
<title>Brightwater Civic Advisors — Home</title>
<link rel="stylesheet" href="https://fonts.googleapis.com/css2?family=Poppins:wght@300;400;500&family=Jost:wght@300;400;600;700&display=swap">
<style>
:root{
  --navy:#31333f;
  --blue:#3a93d6;
  --footer-blue:#3d97d8;
  --paper:#f6fafd;
  --ink:#3b3d42;
  --frame:#5b5f63;
  --nav:#b8bcc6;
  --white:#ffffff;
}
*{box-sizing:border-box;margin:0;padding:0}
html,body{width:1200px;height:797px;overflow:hidden;background:var(--navy)}
body{font-family:"Poppins",sans-serif;color:var(--ink);position:relative}
.site-header{position:absolute;left:0;top:0;width:1200px;height:124px;background:var(--navy)}
.brand{position:absolute;left:225px;top:25px;display:flex;align-items:flex-start;gap:14px}
.brand-mark{width:50px;height:50px;background:var(--blue);margin-top:6px}
.brand-rule{width:1px;height:76px;background:var(--white);opacity:.85}
.brand-name{font-family:"Jost",sans-serif;font-weight:400;color:var(--white);font-size:15px;letter-spacing:4.5px;line-height:19px;text-transform:uppercase;margin-top:3px}
.brand-tagline{font-family:"Jost",sans-serif;font-weight:400;color:var(--white);font-size:6px;letter-spacing:2.6px;text-transform:uppercase;margin-top:6px}
.main-nav{position:absolute;top:56px;left:632px;display:flex;gap:28px;font-size:10px;letter-spacing:.2px}
.main-nav a{color:var(--nav);text-decoration:none;text-transform:uppercase}
.main-nav a.is-active{color:var(--white)}
.about{position:absolute;left:0;top:124px;width:1200px;height:359px;background:var(--paper)}
.portrait{position:absolute;left:225px;top:35px;width:294px;height:294px;border:4px solid var(--frame);background:linear-gradient(135deg,#c9cdd0 0%,#8e8f8c 45%,#3a3433 80%,#2a2a2c 100%)}
.about-copy{position:absolute;left:537px;top:34px;width:430px}
.about-title{font-family:"Jost",sans-serif;font-weight:700;font-size:25px;color:var(--blue);letter-spacing:.5px;line-height:30px;margin-bottom:7px}
.about-copy p{font-size:9.6px;line-height:13.7px;margin-bottom:13.7px;color:var(--ink)}
.btn-more{display:inline-block;margin-top:4px;width:94px;height:25px;line-height:25px;text-align:center;background:var(--navy);color:var(--white);font-size:9.6px;text-decoration:none}
.work-history{position:absolute;left:0;top:483px;width:1200px;height:280px;background:var(--navy)}
.section-title{position:absolute;top:18px;width:1200px;text-align:center;font-family:"Jost",sans-serif;font-size:25px;color:var(--white);font-weight:300;letter-spacing:.5px}
.section-title strong{color:var(--blue);font-weight:600}
.partner{position:absolute;width:206px;height:81px;background:var(--white);display:flex;align-items:center;justify-content:center;gap:8px;font-family:"Poppins",sans-serif;font-weight:500;font-size:13px}
.partner-dot{width:16px;height:16px;flex:none}
.partner-dot.round{border-radius:50%}
.footer{position:absolute;left:0;top:763px;width:1200px;height:34px;background:var(--footer-blue);border-top:3px solid var(--white);color:var(--white);font-size:9.6px;text-align:center;line-height:31px}
</style>
</head>
<body>
<header class="site-header">
  <div class="brand">
    <div class="brand-mark"></div>
    <div class="brand-rule"></div>
    <div>
      <div class="brand-name">Brightwater<br>Civic<br>Advisors</div>
      <div class="brand-tagline">Advancing the common good</div>
    </div>
  </div>
  <nav class="main-nav">
    <a href="#" class="is-active">Home</a>
    <a href="#">Services &amp; Testimonials</a>
    <a href="#">Media &amp; Impact</a>
    <a href="#">Contact</a>
  </nav>
</header>

<section class="about">
  <div class="portrait" role="img" aria-label="Portrait photo of founder Mara Ellison"></div>
  <div class="about-copy">
    <h1 class="about-title">ABOUT</h1>
    <p>Brightwater Civic Advisors supports nonprofit organizations and educational institutions to carry out their missions to benefit the wider community.</p>
    <p>Founder Mara Ellison is an educator with a 22-year record of demonstrated achievement and leadership roles in nonprofits and educational institutions. Most recently, she served as Associate Dean of Students in the University and Director of the Campus Service Center at Lakeshore University. Mara has designed, implemented, and evaluated community-based learning and leadership training programs that have attained positive outcomes documented by survey results, recognition by outside agencies, and grants awarded for new initiatives and expansions. She has also significantly and consistently increased the number of program applicants, volunteers, and community partnerships through innovative programming, improved reputation, targeted recruitment, marketing and communications.</p>
    <p>Mara is a native Chicagoan and has also lived in Tokyo, Boston, San Francisco, and Washington, DC. Mara received her bachelor of arts from Fairhaven College and her masters in education from Kingsbridge University.</p>
    <a href="#" class="btn-more">Keep Reading</a>
  </div>
</section>

<section class="work-history">
  <h2 class="section-title">WORK <strong>HISTORY</strong></h2>
  <div class="partner" style="left:258px;top:69px;color:#7a1a1a"><span class="partner-dot" style="background:#7a1a1a"></span>Campus Service Center</div>
  <div class="partner" style="left:483px;top:69px;color:#1f2a33"><span class="partner-dot round" style="background:#2aa3dc"></span>Meridian Fellows</div>
  <div class="partner" style="left:713px;top:69px;color:#4cb648">Summit Path Schools</div>
  <div class="partner" style="left:258px;top:173px;color:#1d6fa8"><span class="partner-dot" style="background:#e7a823"></span>Civic Learning Lab</div>
  <div class="partner" style="left:483px;top:173px;color:#1a1a1a"><span class="partner-dot round" style="background:#1a1a1a"></span>ServiceCorps</div>
  <div class="partner" style="left:713px;top:173px;color:#1f4fa0">Pacific Teaching Exchange</div>
</section>

<footer class="footer">© 2019, All Rights Reserved, Brightwater Civic Advisors</footer>
</body>
</html>
```